New Business Card for Web Design/Internet Marketing Company

Looking for a great looking new business card. We are a 10 year old web design, internet marketing and website management company that works mostly with small businesses.

Our new card needs to better match the colors and style of our website, be bold, extremely usable and slightly edgy.

Target Market(s)

Small/Medium businesses that have websites

Industry/Entity Type

Internet

Requirements
Must have
• Front and back design, full color, rounded corners please

Must use the colors/style of our website (JPG provided)

INFO FOR CARDS (as readable as possible please)
Mark Lenner
President/CEO
mark@trelvanmedia.example
Phone: 520-381-7459
Toll Free: 866-381-7459
Address: 4315 W. Calloway Ave. Ste. 140, Tucson, AZ 85792

THINGS I WANT TO PROMOTE (if there is room):
1. Our Website - www.trelvanmedia.example

2. Social Media
Twitter: @trelvanmedia
Facebook: www.facebook.com/trelvanmedia

3. Our Services
Web Design
Internet Marketing
Website Management

```html
<!DOCTYPE html>
<html lang="en">
<head>
<meta charset="utf-8">
<title>Trelvan Media Business Card</title>
<link rel="stylesheet" href="https://fonts.googleapis.com/css2?family=Open+Sans:ital,wght@0,400;0,600;0,700;1,700&display=swap">
<style>
  :root {
    --stage: #1d1d1f;
    --brand-blue: #0a6ea8;
    --brand-orange: #e8661c;
    --card-white: #f5f5f4;
    --ink-grey: #626262;
    --ink-dark: #4a4a4a;
    --on-blue: #ffffff;
  }
  * { margin: 0; padding: 0; box-sizing: border-box; }
  html, body { width: 1200px; height: 500px; overflow: hidden; }
  body {
    background: var(--stage);
    font-family: "Open Sans", sans-serif;
    position: relative;
  }
  .card {
    position: absolute;
    top: 110px;
    width: 493px;
    height: 280px;
    border-radius: 28px;
    overflow: hidden;
  }
  .card-back { left: 100px; background: var(--brand-blue); color: var(--on-blue); }
  .card-front { left: 607px; background: var(--card-white); }

  /* Brand name */
  .brand {
    display: flex;
    align-items: center;
    gap: 8px;
    position: absolute;
  }
  .brand-dot {
    width: 14px; height: 14px; border-radius: 50%;
    background: var(--brand-orange);
  }
  .brand-name {
    font-weight: 700;
    color: var(--brand-orange);
    white-space: nowrap;
  }
  .card-back .brand { top: 110px; left: 0; right: 0; justify-content: center; }
  .card-back .brand-name { font-size: 22px; }
  .card-front .brand { top: 48px; left: 24px; }
  .card-front .brand-name { font-size: 30px; }
  .front-accent-bar {
    position: absolute; left: 13px; top: 30px;
    width: 5px; height: 46px; background: var(--brand-blue);
  }

  /* Back: contact block */
  .office {
    position: absolute; left: 21px; top: 197px;
    font-size: 14px; line-height: 21.5px; font-style: normal;
  }
  .divider {
    position: absolute; left: 216px; top: 198px;
    width: 2px; height: 62px; background: rgba(255,255,255,0.8);
  }
  .links {
    position: absolute; left: 233px; top: 197px;
    list-style: none; font-size: 14px; line-height: 21.5px;
  }
  .links li { display: flex; align-items: center; gap: 8px; }
  .link-square {
    width: 15px; height: 15px; border-radius: 3px;
    background: var(--brand-orange);
  }

  /* Front: swoosh */
  .swoosh { position: absolute; inset: 0; }

  /* Front: services */
  .services { position: absolute; left: 21px; top: 170px; }
  .services-title {
    font-size: 16px; font-weight: 700; font-style: italic;
    color: var(--brand-orange); margin-bottom: 1px;
  }
  .services-title .accent { color: var(--brand-blue); }
  .service-list { list-style: none; font-size: 16px; line-height: 22.5px; color: var(--ink-dark); }
  .service-list li { display: flex; align-items: center; gap: 8px; }
  .service-bullet {
    width: 8px; height: 8px; border-radius: 50%;
    background: var(--brand-blue);
  }

  /* Front: person */
  .person {
    position: absolute; right: 22px; top: 142px; text-align: right;
  }
  .person-name { font-size: 27px; color: var(--ink-grey); letter-spacing: 0.5px; line-height: 32px; }
  .person-title { font-size: 15px; color: var(--brand-orange); line-height: 20px; }
  .person-phone { font-size: 17px; color: var(--brand-blue); font-weight: 600; margin-top: 22px; line-height: 22px; }
  .person-email { font-size: 15.5px; color: var(--ink-dark); line-height: 22px; }
</style>
</head>
<body>

  <section class="card card-back" aria-label="Card back">
    <div class="brand">
      <span class="brand-dot"></span>
      <span class="brand-name">Trelvan Media</span>
    </div>
    <address class="office">
      Toll Free: 866-381-7459<br>
      4315 W. Calloway Ave.<br>
      Ste. 140, Tucson, AZ 85792
    </address>
    <div class="divider"></div>
    <ul class="links">
      <li><span class="link-square"></span>@trelvanmedia</li>
      <li><span class="link-square"></span>facebook.com/trelvanmedia</li>
      <li><span class="link-square"></span>www.trelvanmedia.example</li>
    </ul>
  </section>

  <section class="card card-front" aria-label="Card front">
    <svg class="swoosh" width="493" height="280" viewBox="0 0 493 280" aria-hidden="true">
      <path d="M418 52 C305 88 232 176 214 280 L240 280 C254 186 318 104 418 52 Z" fill="var(--brand-blue)"/>
      <path d="M420 280 C450 272 475 262 493 250 L493 280 Z" fill="var(--brand-blue)"/>
    </svg>
    <div class="front-accent-bar"></div>
    <div class="brand">
      <span class="brand-dot"></span>
      <span class="brand-name">Trelvan Media</span>
    </div>

    <div class="services">
      <p class="services-title"><span class="accent">Our</span> Services</p>
      <ul class="service-list">
        <li><span class="service-bullet"></span>Web Design</li>
        <li><span class="service-bullet"></span>Internet Marketing</li>
        <li><span class="service-bullet"></span>Website Management</li>
      </ul>
    </div>

    <div class="person">
      <p class="person-name">MARK LENNER</p>
      <p class="person-title">President/CEO</p>
      <p class="person-phone">520-381-7459</p>
      <p class="person-email">mark@trelvanmedia.example</p>
    </div>
  </section>

</body>
</html>
```